Business card and stationery for School
Business card and stationery for School - Education
Creative Brief
Use same font as used in my logo
However variations is permitted
Bright & Fun-filled
Mrs Ifeoma C. Nwachukwu
Proprietress
Plot 147D KC4 Mbelu Estate Opposite TRB Office Sirenko Road, Dunam FCT, Abuja
info@lumbeekids.example
www.lumbeekids.example

```html
<!DOCTYPE html>
<html lang="en">
<head>
<meta charset="utf-8">
<title>Lumbee Kids Academy — Business Card</title>
<link href="https://fonts.googleapis.com/css2?family=Open+Sans:ital,wght@0,400;0,600;0,700;1,400&display=swap" rel="stylesheet">
<style>
  :root {
    --bg: #ece9e4;
    --card-white: #ffffff;
    --purple: #8a1a7e;
    --purple-deep: #6b0f62;
    --green: #6fa52b;
    --green-dark: #5a8a1f;
    --yellow: #f2b51c;
    --grey-text: #6d6d6d;
    --cream-text: #fbe9a8;
  }
  * { box-sizing: border-box; margin: 0; padding: 0; }
  html, body { width: 1200px; height: 751px; overflow: hidden; }
  body {
    background: var(--bg);
    font-family: "Open Sans", Arial, sans-serif;
    position: relative;
  }
  .card {
    position: absolute;
    width: 520px;
    height: 300px;
    border-radius: 14px;
    overflow: hidden;
    box-shadow: 0 6px 18px rgba(0,0,0,0.18);
  }
  /* Front */
  .card-front { left: 50px; top: 225px; background: var(--card-white); }
  .brand {
    position: absolute; left: 26px; top: 150px;
    width: 240px;
    display: flex; align-items: center; gap: 7px;
  }
  .brand-dot { width: 13px; height: 13px; border-radius: 50%; background: var(--green); flex: none; }
  .brand-name {
    font-weight: 700; font-size: 15px; color: var(--purple);
    letter-spacing: 0.3px; text-transform: uppercase; white-space: nowrap;
  }
  .holder { position: absolute; left: 290px; top: 40px; width: 215px; }
  .holder-name { font-weight: 700; font-size: 16px; color: var(--purple); white-space: nowrap; }
  .holder-role { font-size: 10px; color: var(--grey-text); margin-top: 1px; }
  .address {
    margin-top: 14px; font-size: 10px; line-height: 1.4; color: var(--grey-text);
  }
  .contacts { list-style: none; margin-top: 14px; font-size: 10px; color: var(--grey-text); line-height: 1.55; }
  .contacts li { display: flex; align-items: center; gap: 6px; }
  .contacts svg { width: 9px; height: 9px; fill: var(--green); flex: none; }
  .accent-line { position: absolute; left: 0; right: 0; top: 226px; height: 3px; background: var(--yellow); }
  .band {
    position: absolute; left: 0; right: 0; top: 232px; height: 30px;
    background: linear-gradient(var(--green), var(--green-dark));
    display: flex; align-items: center; padding-left: 216px;
  }
  .band-text { font-style: italic; font-size: 13px; color: var(--cream-text); }
  .band-line { position: absolute; left: 0; right: 0; top: 265px; height: 2px; background: var(--purple); }
  /* Back */
  .card-back {
    left: 630px; top: 225px;
    background: radial-gradient(circle at 50% 40%, #a52a98 0%, var(--purple) 45%, var(--purple-deep) 100%);
    display: flex; flex-direction: column; align-items: center; justify-content: center;
  }
  .back-brand { display: flex; align-items: center; gap: 10px; margin-top: -10px; }
  .back-dot { width: 20px; height: 20px; border-radius: 50%; background: #ffffff; }
  .back-name { font-weight: 700; font-size: 24px; color: #ffffff; letter-spacing: 0.5px; text-transform: uppercase; }
  .back-web { margin-top: 22px; font-size: 12px; color: #ffffff; letter-spacing: 0.4px; }
</style>
</head>
<body>
  <section class="card card-front" aria-label="Business card front">
    <div class="brand">
      <span class="brand-dot"></span>
      <span class="brand-name">Lumbee Kids Academy</span>
    </div>
    <div class="holder">
      <p class="holder-name">Mrs Ifeoma C. Nwachukwu</p>
      <p class="holder-role">Proprietress</p>
      <p class="address">Plot 147D KC4 Mbelu Estate<br>Opposite TRB Office<br>Sirenko Road, Dunam<br>FCT, Abuja</p>
      <ul class="contacts">
        <li><svg viewBox="0 0 10 10"><path d="M2 0h2l1 3-1.5 1a6 6 0 0 0 2.5 2.5L7 5l3 1v2a2 2 0 0 1-2 2A8 8 0 0 1 0 2a2 2 0 0 1 2-2z"/></svg>+234.801.555.0142</li>
        <li><svg viewBox="0 0 10 10"><path d="M2 0h2l1 3-1.5 1a6 6 0 0 0 2.5 2.5L7 5l3 1v2a2 2 0 0 1-2 2A8 8 0 0 1 0 2a2 2 0 0 1 2-2z"/></svg>+234.803.555.0187</li>
        <li><svg viewBox="0 0 10 10"><path d="M0 2h10v6H0z M0 2l5 3.5L10 2" /></svg>info@lumbeekids.example</li>
      </ul>
    </div>
    <div class="accent-line"></div>
    <div class="band"><span class="band-text">"Creche, Nursery &amp; Primary"</span></div>
    <div class="band-line"></div>
  </section>

  <section class="card card-back" aria-label="Business card back">
    <div class="back-brand">
      <span class="back-dot"></span>
      <span class="back-name">Lumbee Kids</span>
    </div>
    <p class="back-web">www.lumbeekids.example</p>
  </section>
</body>
</html>
```